Social Media Graphics - Oakline Push REVISED

Create 6-7 individual social media graphics (square size) to encourage folks to join our online course called:

The Harvest Ledger Circle
How to Launch a Multi-Million Business From Scratch
Sign Up Today!

IMPORTANT: Make the largest and most prominent text on the graphic be: How to Launch a Multi-Million Business From Scratch

For the color scheme of the graphics, let's try a blue color palette; make sure the graphics appeal to both men and women

Make sure each graphic contains 1 of the 3 pics attached (crop pic as needed); and make sure one of the graphics is all TEXT only.

Target Market(s)

men and women looking to start a business

Industry/Entity Type

Entrepreneurship

Colors
0054AA
0677BA
7BADD7
CADEEF
E8F1F8

Requirements
Must have
• All the text and use the 3 pics provided; one graphic can be all text; Simple, modern design that's easy to read

```html
<!DOCTYPE html>
<html lang="en">
<head>
<meta charset="utf-8">
<title>The Harvest Ledger Circle – Social Graphics</title>
<link href="https://fonts.googleapis.com/css2?family=Oswald:wght@400;500;600&family=Montserrat:wght@700;800&display=swap" rel="stylesheet">
<style>
  :root{
    --blue-deep:#0054AA;
    --blue-mid:#0677BA;
    --blue-soft:#7BADD7;
    --blue-pale:#CADEEF;
    --blue-mist:#E8F1F8;
    --ink:#111318;
    --white:#ffffff;
    --board:#d6d6d6;
  }
  *{margin:0;padding:0;box-sizing:border-box}
  html,body{width:1200px;height:809px;overflow:hidden;background:var(--board)}
  .board{position:relative;width:1200px;height:809px;background:var(--board)}
  .tile{position:absolute;width:373px;height:373px;overflow:hidden}
  .headline{font-family:"Oswald",sans-serif;font-weight:500;text-transform:uppercase;position:absolute;z-index:2}
  .brand{font-family:"Montserrat",sans-serif;font-weight:800;text-transform:uppercase;letter-spacing:.3px;z-index:2}
  .photo{position:absolute;z-index:1}
  .cta{font-family:"Oswald",sans-serif;font-weight:600;text-transform:uppercase;position:absolute;display:flex;align-items:center;justify-content:center;font-size:11px;letter-spacing:.2px;z-index:2}
  .cta--outline{border:1.5px solid var(--white);border-radius:14px;color:var(--white)}
  .cta--solid{background:var(--blue-deep);border-radius:14px;color:var(--white)}
  .cta--link{text-decoration:underline;text-underline-offset:2px}

  /* tile 1 */
  .tile--arch{left:20px;top:20px;background:linear-gradient(180deg,var(--blue-soft) 0%,var(--blue-mid) 55%,var(--blue-deep) 100%)}
  .arch{left:16px;top:30px;width:181px;height:298px;border:2px solid var(--white);border-bottom:none;border-radius:90px 90px 0 0;overflow:hidden}
  .arch .fill{width:100%;height:100%;background:linear-gradient(180deg,#e9e2d8 0%,#a89884 45%,#3a3b45 100%)}
  .tag-dark{position:absolute;background:var(--ink);color:var(--white);border-radius:5px;padding:3px 8px;font-size:14px;white-space:nowrap}
  .tile--arch .stack{position:absolute;left:206px;width:156px;text-align:center;color:var(--blue-pale);font-size:20px;line-height:31px;top:135px}

  /* tile 2 */
  .tile--duo{left:412px;top:20px;background:linear-gradient(180deg,var(--blue-mist) 0%,var(--blue-pale) 45%,var(--blue-mid) 80%,var(--blue-deep) 100%)}
  .pill-blue{position:absolute;background:var(--blue-deep);color:var(--white);border-radius:20px;display:flex;align-items:center;justify-content:center}
  .block{position:absolute;left:10px;color:var(--white);font-size:20px;line-height:24px;padding:0 5px;border-radius:3px}
  .block--dark{background:var(--ink)}
  .block--blue{background:var(--blue-deep)}

  /* tile 3 */
  .tile--text{left:802px;top:20px;background:linear-gradient(180deg,var(--blue-mist) 0%,var(--blue-pale) 50%,var(--blue-mid) 100%)}
  .tile--text .money{left:0;top:170px;width:373px;height:203px;background:linear-gradient(180deg,rgba(202,222,239,0) 0%,rgba(123,173,215,.6) 45%,rgba(6,119,186,.85) 100%)}

  /* tile 4 */
  .tile--banner{left:20px;top:406px;background:linear-gradient(180deg,var(--blue-mist) 0%,var(--blue-pale) 60%,var(--blue-soft) 100%)}
  .banner{position:absolute;left:0;top:17px;width:328px;height:43px;z-index:2}
  .tile--banner .stack{position:absolute;right:8px;width:160px;text-align:right;color:var(--ink);font-size:21px;line-height:31px;top:100px}

  /* tile 5 & 6 */
  .tile--lower{left:412px;top:410px;background:linear-gradient(180deg,var(--blue-pale) 0%,var(--blue-mid) 55%,var(--blue-deep) 100%)}
  .tile--center{left:802px;top:406px;background:linear-gradient(180deg,var(--blue-mist) 0%,var(--blue-soft) 40%,var(--blue-mid) 70%,var(--blue-deep) 100%)}
  .pill-white{position:absolute;background:var(--white);color:var(--blue-deep);border-radius:20px;display:flex;align-items:center;justify-content:center;font-size:13.5px;white-space:nowrap}
</style>
</head>
<body>
<main class="board">

  <!-- Tile 1 -->
  <section class="tile tile--arch">
    <div class="photo arch"><div class="fill" role="img" aria-label="Photo of the two course hosts speaking on stage"></div></div>
    <div class="brand tag-dark" style="left:211px;top:65px">The Harvest</div>
    <div class="brand tag-dark" style="left:203px;top:94px">Ledger Circle</div>
    <div class="headline stack">How to launch a<br>multi-million<br>business from<br>scratch</div>
    <div class="cta cta--outline" style="left:224px;top:275px;width:117px;height:24px">Sign up today!</div>
  </section>

  <!-- Tile 2 -->
  <section class="tile tile--duo">
    <div class="photo" style="left:178px;top:95px;width:195px;height:278px;background:linear-gradient(180deg,rgba(40,34,36,0) 0%,#3a2f31 25%,#c9304e 60%,#1a1a1f 100%)" role="img" aria-label="Photo of the two course hosts standing with arms crossed"></div>
    <div class="pill-blue brand" style="left:58px;top:30px;width:254px;height:37px;font-size:13px">The Harvest Ledger Circle</div>
    <div class="headline block block--dark" style="top:107px">How to launch a</div>
    <div class="headline block block--dark" style="top:138px">Multi-million</div>
    <div class="headline block block--blue" style="top:169px">Business from</div>
    <div class="headline block block--blue" style="top:200px">Scratch</div>
    <div class="cta cta--link" style="left:15px;top:233px;height:18px;color:var(--blue-deep);font-size:12px">Sign up today!</div>
  </section>

  <!-- Tile 3: text only -->
  <section class="tile tile--text">
    <div class="photo money" role="img" aria-label="Faded photo of scattered banknotes"></div>
    <div class="brand" style="position:absolute;left:0;width:373px;top:43px;text-align:center;color:var(--blue-deep);font-size:15px">The Harvest Ledger</div>
    <div class="brand" style="position:absolute;left:0;width:373px;top:62px;text-align:center;color:var(--blue-deep);font-size:38px;line-height:46px">Circle</div>
    <div class="headline" style="left:0;width:373px;top:122px;text-align:center;color:var(--ink);font-size:21px;line-height:30px;font-weight:400">How to launch a multi-million<br>business from scratch</div>
    <div class="cta cta--solid" style="left:127px;top:192px;width:118px;height:24px">Sign up today!</div>
  </section>

  <!-- Tile 4 -->
  <section class="tile tile--banner">
    <div class="photo" style="left:0;top:73px;width:205px;height:300px;background:linear-gradient(90deg,rgba(202,222,239,0) 0%,rgba(202,222,239,0) 80%,rgba(202,222,239,.9) 100%),linear-gradient(180deg,#3a2f31 0%,#c9304e 55%,#1a1a1f 100%)" role="img" aria-label="Photo of the two course hosts smiling with arms crossed"></div>
    <svg class="banner" viewBox="0 0 328 43" aria-hidden="true"><polygon points="0,0 305,0 328,43 0,43" fill="#0054AA"/></svg>
    <div class="brand" style="position:absolute;left:17px;top:17px;height:43px;display:flex;align-items:center;color:var(--white);font-size:15.5px">The Harvest Ledger Circle</div>
    <div class="headline stack">How to launch a<br>multi-million<br>business from<br>scratch</div>
    <div class="cta cta--solid" style="left:249px;top:231px;width:118px;height:24px">Sign up today!</div>
  </section>

  <!-- Tile 5 -->
  <section class="tile tile--lower">
    <div class="photo" style="left:120px;top:0;width:253px;height:190px;background:linear-gradient(180deg,rgba(26,26,31,0) 0%,#1e1e24 40%,#1c4d8a 100%)" role="img" aria-label="Photo of the two course hosts in front of a banknote backdrop"></div>
    <div class="pill-white brand" style="left:16px;top:192px;width:254px;height:36px">The Harvest Ledger Circle</div>
    <div class="headline" style="left:18px;top:238px;color:var(--white);font-size:21px;line-height:30px">How to launch a multi-million<br>business from scratch</div>
    <div class="cta cta--outline" style="left:20px;top:304px;width:117px;height:23px">Sign up today!</div>
  </section>

  <!-- Tile 6 -->
  <section class="tile tile--center">
    <div class="photo" style="left:69px;top:8px;width:230px;height:202px;background:linear-gradient(180deg,rgba(58,47,49,.2) 0%,#3a2f31 35%,#c9304e 70%,#1a1a1f 100%)" role="img" aria-label="Photo of the two course hosts standing side by side"></div>
    <div class="pill-white brand" style="left:59px;top:210px;width:252px;height:36px">The Harvest Ledger Circle</div>
    <div class="headline" style="left:0;width:373px;top:257px;text-align:center;color:var(--white);font-size:21px;line-height:29px">How to launch a multi-million<br>business from scratch</div>
    <div class="cta cta--link" style="left:0;width:373px;top:317px;height:18px;color:var(--white);font-size:12px">Sign up today!</div>
  </section>

</main>
</body>
</html>
```